I need a SEO-friendly Wordpress website (making sure to style H1, H2, H3, etc correctly) for a Hawaii-based law firm called Meridian Crest Legal Group. Comparable websites include https://brvlaw.example/ and https://www.lomrit.example/ for design reference. The current copy on the TarnAdvocate.example website can be used.

```html
<!DOCTYPE html>
<html lang="en">
<head>
<meta charset="utf-8">
<title>Meridian Crest Legal Group</title>
<link href="https://fonts.googleapis.com/css2?family=Lato:wght@700;900&family=Montserrat:wght@500;600&family=Open+Sans:wght@400;600;700&display=swap" rel="stylesheet">
<style>
:root{
  --brand:#9a4a10;
  --brand-dark:#7a2a0c;
  --ink:#111;
  --text:#333;
  --line:#8a8a8a;
  --footer:#2a2a2a;
  --white:#fff;
}
*{box-sizing:border-box;margin:0;padding:0}
html,body{width:1200px;height:2546px;overflow:hidden;background:var(--white);font-family:"Open Sans",Arial,sans-serif;color:var(--text)}
.page{position:relative;width:1200px;height:2546px}
.abs{position:absolute}
.topbar{left:0;top:0;width:1200px;height:42px;background:var(--brand);color:var(--white);font-size:16px;font-weight:600}
.topbar .contact{position:absolute;top:10px;display:flex;align-items:center;gap:6px}
.topbar svg{width:14px;height:14px}
.social{position:absolute;right:112px;top:14px;display:flex;gap:10px}
.social span{width:14px;height:14px;border-radius:50%;background:var(--white);display:block}
.brand{left:110px;top:50px;font-family:"Montserrat",sans-serif;color:var(--ink);line-height:1}
.brand .name{font-size:38px;font-weight:600;letter-spacing:-.5px}
.brand .sub{font-size:22px;font-weight:500;margin-top:4px}
.nav{top:78px;display:flex;gap:38px;right:112px;font-size:17px;font-weight:600;color:var(--ink)}
.nav a{color:inherit;text-decoration:none;position:relative}
.nav a.active::after{content:"";position:absolute;left:0;right:0;bottom:-9px;height:3px;background:var(--brand-dark)}
.hero{left:0;top:127px;width:1200px;height:600px;background:linear-gradient(120deg,#6b3413 0%,#a8642c 30%,#c88a4d 50%,#8a4a1f 75%,#4a2410 100%)}
.card{background:var(--white);border:1px solid #ccc;border-bottom:2px solid var(--line)}
.about{left:111px;top:692px;width:607px;height:394px;padding:48px 12px 0 13px}
h1{font-family:"Lato",sans-serif;font-weight:900;font-size:36px;line-height:34px;color:var(--ink);letter-spacing:-.3px}
.about h2{font-size:20px;font-weight:600;color:var(--brand);margin:28px 0 18px -1px}
.about p{font-size:14px;line-height:34px}
.more{display:inline-block;margin-top:18px;font-weight:700;font-size:16px;color:var(--brand-dark);text-decoration:none}
.quote{left:747px;top:692px;width:341px;height:394px;padding:26px 34px 0}
.quote h3{font-family:"Lato",sans-serif;font-weight:700;font-size:26px;color:var(--ink);margin-bottom:27px}
.field{border:1px solid #555;height:37px;font-size:14px;color:#555;padding:8px 10px;margin-bottom:11px}
.row{display:flex;gap:11px}.row .field{flex:1}
.field.msg{height:85px}
.btn{background:var(--brand-dark);color:var(--white);text-align:center;font-weight:700;font-size:16px;height:38px;line-height:38px;border:1px solid #333}
h2.section{font-family:"Lato",sans-serif;font-weight:900;font-size:40px;color:var(--ink);text-align:center;width:1200px;left:0}
.tile{top:1246px;width:236px;height:176px;border:1px solid #bbb;overflow:hidden}
.tile .img{height:134px}
.tile .label{height:42px;background:#a4581b;color:var(--white);text-align:center;font-size:22px;font-weight:600;line-height:42px}
.post{top:1577px;width:305px;height:203px;border:1px solid #555;padding:26px 13px 0;font-size:13.5px;line-height:28.5px;color:#222}
.post .date{text-align:center;font-size:14px;font-weight:600;color:#222;margin-bottom:4px}
.map{left:0;top:1867px;width:1200px;height:458px;background:linear-gradient(90deg,#a9c8ec 0%,#cfdcea 14%,#ececea 22%,#e9eae6 60%,#eef0ea 100%)}
.footer{left:0;top:2325px;width:1200px;height:221px;background:var(--footer);color:var(--white)}
.fi{position:absolute;top:54px;display:flex;align-items:center;gap:20px;font-size:16.5px;font-weight:600;line-height:26px}
.fi .box{width:50px;height:60px;background:var(--white);display:flex;align-items:center;justify-content:center}
.fnav{position:absolute;top:122px;left:0;width:1200px;display:flex;justify-content:center;gap:54px;font-size:17px;font-weight:600}
.copy{position:absolute;top:185px;width:1200px;text-align:center;font-size:14px}
</style>
</head>
<body>
<div class="page">
  <header class="abs topbar">
    <div class="contact" style="left:115px"><svg viewBox="0 0 24 24" fill="#fff"><path d="M6.6 10.8a15 15 0 006.6 6.6l2.2-2.2c.3-.3.7-.4 1-.2 1.1.4 2.3.6 3.6.6.6 0 1 .4 1 1V20c0 .6-.4 1-1 1A17 17 0 013 4c0-.6.4-1 1-1h3.5c.6 0 1 .4 1 1 0 1.3.2 2.5.6 3.6.1.3 0 .7-.2 1z"/></svg>+1.808.555.0147</div>
    <div class="contact" style="left:286px"><svg viewBox="0 0 24 24" fill="none" stroke="#fff" stroke-width="2"><rect x="3" y="5" width="18" height="14"/><path d="M3 6l9 7 9-7"/></svg>clients@tarnadvocate.example</div>
    <div class="social"><span></span><span></span><span></span><span></span></div>
  </header>

  <div class="abs brand"><div class="name">MERIDIAN CREST</div><div class="sub">LEGAL GROUP</div></div>
  <nav class="abs nav"><a class="active" href="#">HOME</a><a href="#">PRACTICE AREAS ▾</a><a href="#">ATTORNEYS</a><a href="#">BLOG</a><a href="#">CONTACT US</a></nav>

  <div class="abs hero" role="img" aria-label="Group photo of the firm's attorneys in a wood-panelled office"></div>

  <section class="abs card about">
    <h1>ABOUT THE KONA LAWYERS<br>OF MCLG</h1>
    <h2>Lawyers Serving the Big Island and Neighboring Islands</h2>
    <p>The experienced attorneys in the Meridian Crest Legal Group's Kailua Kona, Hawaii office provide clients with a wide range of litigation expertise, including legal claims involving divorce &amp; family, personal injury, toxic exposures, intellectual property, and real estate.</p>
    <a class="more" href="#">READ MORE ⊕</a>
  </section>

  <aside class="abs card quote">
    <h3>GET A FREE QUOTE</h3>
    <div class="row"><div class="field">First Name</div><div class="field">Last Name</div></div>
    <div class="field">phone</div>
    <div class="field">Enter Your Email</div>
    <div class="field msg">Message</div>
    <div class="btn">GET STARTED</div>
  </aside>

  <h2 class="abs section" style="top:1166px">PRACTICE AREAS</h2>
  <div class="abs tile" style="left:111px"><div class="img" role="img" aria-label="Gold wedding rings" style="background:linear-gradient(#f4f0e6,#d9b84a)"></div><div class="label">FAMILY &amp; DIVORCE</div></div>
  <div class="abs tile" style="left:359px"><div class="img" role="img" aria-label="Damaged car after a crash" style="background:linear-gradient(135deg,#2c3c66,#7b8db0 50%,#3a3a3a)"></div><div class="label">PERSONAL INJURY</div></div>
  <div class="abs tile" style="left:607px"><div class="img" role="img" aria-label="Dimly lit corporate interior" style="background:linear-gradient(#2a2520,#6a5a3a 60%,#b8862e)"></div><div class="label">CORPORATE &amp; IP</div></div>
  <div class="abs tile" style="left:855px"><div class="img" role="img" aria-label="Ocean view through a window" style="background:linear-gradient(90deg,#3b4a3e,#9fc6e6 40%,#c9dff0)"></div><div class="label">REAL ESTATE</div></div>

  <h2 class="abs section" style="top:1496px">OUR BLOG</h2>
  <article class="abs post" style="left:112px"><div class="date">📅July 30,2019</div>❝ Lorem ipsum dolor sit ameddd, consec-tufgr adi;piscing elit, sed do eiusmoidunt ut labore et dolore magna aliqua. Quis ipsum spehfgfe ultrices gravida. Risus commodo ❞</article>
  <article class="abs post" style="left:448px"><div class="date">📅July 30,2019</div>❝ Lorem ipsum dolor sit ameddd, consec-tufgr adi;piscing elit, sed do eiusmoidunt ut labore et dolore magna aliqua. Quis ipsum spehfgfe ultrices gravida. Risus commodo ❞</article>
  <article class="abs post" style="left:783px"><div class="date">📅July 30,2019</div>❝ Lorem ipsum dolor sit ameddd, consec-tufgr adi;piscing elit, sed do eiusmoidunt ut labore et dolore magna aliqua. Quis ipsum spehfgfe ultrices gravida. Risus commodo ❞</article>

  <div class="abs map" role="img" aria-label="Street map showing the office location in Kailua Kona"></div>

  <footer class="abs footer">
    <div class="fi" style="left:110px"><div class="box"><svg width="24" height="32" viewBox="0 0 24 32"><path d="M12 1a10 10 0 00-10 10c0 8 10 20 10 20s10-12 10-20A10 10 0 0012 1z" fill="#a4581b"/><circle cx="12" cy="11" r="4" fill="#fff"/></svg></div><div>82-1140 Lanakila Road, Suite 210<br>Kailua Kona, Hawaii 96799.</div></div>
    <div class="fi" style="left:541px"><div class="box"><svg width="30" height="30" viewBox="0 0 24 24" fill="#a4581b"><path d="M6.6 10.8a15 15 0 006.6 6.6l2.2-2.2c.3-.3.7-.4 1-.2 1.1.4 2.3.6 3.6.6.6 0 1 .4 1 1V20c0 .6-.4 1-1 1A17 17 0 013 4c0-.6.4-1 1-1h3.5c.6 0 1 .4 1 1 0 1.3.2 2.5.6 3.6.1.3 0 .7-.2 1z"/></svg></div><div>+1.808.555.0147</div></div>
    <div class="fi" style="left:823px"><div class="box"><svg width="34" height="26" viewBox="0 0 24 18" fill="none" stroke="#a4581b" stroke-width="2"><rect x="1" y="1" width="22" height="16"/><path d="M1 2l11 8 11-8"/></svg></div><div>clients@tarnadvocate.example</div></div>
    <nav class="fnav"><span>HOME</span><span>PRACTICE AREAS</span><span>ATTORNEYS</span><span>BLOG</span><span>CONTACT US</span></nav>
    <div class="copy">Copyright © 2019. All Rights Reserved</div>
  </footer>
</div>
</body>
</html>
```